Company Flyer for Electric boating company

I am looking for a company flyer which we can hand over to boat owners in the Netherlands (Amsterdam area). Our core business is to rebuild every boat (from 4 to 10 meters) into an electrically propelled boat. We are taking out diesels and replace them with a high quality electrical motor, inboard varying from 30 till 80 pk (hp). And outboard from 1pk (hp) till 200pk. We are the best, not the cheapest, not the most expensive. We only work with the best materials. The flyer has to be sort of in line with our website and branding.

Major advantages of electric boating are:
- completely silent
- no fumes, smells or smoke
- cheap to operate
- environmentally friendly
- obliged in more and more areas
- no maintenance
- more enjoyable

The flyer should be A5 format. Since all the text has to be in Dutch I expect only the graphical design and layout for advantages, process, pricing and contact details etc.

Target Market(s)

Boat owners in the Netherlands

Font styles to use
Sans Serif

Colors
9bcb3c
add136
cadf82
0555a3
3176b5
85acd3
e0ebf3

Requirements
Must have
• Clean design, in line with website: www.volthaven.nl
Nice to have
• icons for advantages, boating etc

2 sides
Should not have
• Steering wheel...

```html
<!DOCTYPE html>
<html lang="nl">
<head>
<meta charset="utf-8">
<title>Volthaven – Boating Company flyer</title>
<link href="https://fonts.googleapis.com/css2?family=Montserrat:wght@400;500;600;700;800&family=Open+Sans:wght@400;600;700&display=swap" rel="stylesheet">
<style>
  :root{
    --green:#8cc63f;
    --green-bright:#9bcb3c;
    --green-soft:#cadf82;
    --black:#0d0d0d;
    --ink:#222;
    --grey:#666;
    --rule:#c9c9c9;
    --white:#fff;
    --sea-dark:#1d3346;
    --sea-light:#9fb6c6;
  }
  *{box-sizing:border-box;margin:0;padding:0}
  html,body{width:847px;height:1200px;overflow:hidden;background:var(--white)}
  body{font-family:"Open Sans",Arial,sans-serif;color:var(--ink)}
  .flyer{position:relative;width:847px;height:1200px;overflow:hidden;background:var(--white)}

  /* header */
  .hero-panel{position:absolute;left:0;top:0;width:440px;height:415px;background:var(--black);padding:22px 30px 0 30px;color:var(--white)}
  .brand{display:flex;align-items:center;gap:14px}
  .brand-dot{width:46px;height:46px;border-radius:50%;background:var(--green)}
  .brand-name{font-family:"Montserrat",sans-serif;font-weight:800;font-size:30px;color:var(--green);letter-spacing:1px;line-height:1}
  .brand-tag{font-family:"Montserrat",sans-serif;font-size:10px;letter-spacing:2px;color:var(--white);margin-top:4px}
  .hero-title{font-family:"Montserrat",sans-serif;font-weight:700;font-size:60px;line-height:1.02;margin-top:40px}
  .hero-title .accent{color:var(--green)}
  .hero-sub{font-family:"Montserrat",sans-serif;font-weight:500;font-size:21px;line-height:1.2;margin-top:22px;text-transform:uppercase}
  .hero-sub b{color:var(--green);font-weight:700}
  .hero-note{font-family:"Montserrat",sans-serif;font-size:21px;margin-top:12px}
  .hero-note b{color:var(--green);font-weight:700}
  .hero-photo{position:absolute;left:440px;top:0;width:407px;height:560px;background:linear-gradient(160deg,var(--sea-light) 0%,#5f7d95 40%,var(--sea-dark) 100%)}

  /* intro */
  .intro{position:absolute;left:30px;top:420px;width:400px}
  .section-title{font-family:"Montserrat",sans-serif;font-weight:500;font-size:22px;color:var(--ink);text-transform:uppercase;letter-spacing:.5px}
  .body-copy{border-left:2px solid var(--ink);padding-left:12px;margin:14px 0 0 40px;font-size:12.5px;line-height:1.45;color:var(--grey)}
  .body-copy b{color:var(--ink)}
  .body-copy + .body-copy{margin-top:12px}

  /* pricing */
  .pricing{position:absolute;left:10px;top:572px;width:827px;display:flex;gap:16px}
  .plan{width:195px}
  .plan-card{background:var(--green);color:var(--white);text-align:center;padding:12px 10px 12px;height:158px}
  .plan-icon{display:block;margin:0 auto 4px}
  .plan-name{font-family:"Montserrat",sans-serif;font-weight:700;font-size:21px;line-height:1}
  .plan-size{font-size:9px;letter-spacing:1px;margin-top:2px}
  .plan-price{margin-top:14px;border-top:1px solid rgba(255,255,255,.55);padding-top:8px}
  .plan-from{font-size:9px;text-transform:uppercase;letter-spacing:1px}
  .plan-amount{font-family:"Montserrat",sans-serif;font-weight:700;font-size:30px;line-height:1.05}
  .plan-amount small{font-size:15px;font-weight:600;margin-right:4px}
  .plan-amount.request{font-size:21px;line-height:1.5}
  .plan-note{margin-top:8px;font-size:10px;line-height:1.4;color:var(--green);text-align:center;padding:0 10px}

  /* solution */
  .solution{position:absolute;left:30px;top:868px;width:400px}

  /* advantages */
  .advantages{position:absolute;left:462px;top:862px;width:370px;height:318px;border:2px solid var(--rule);padding:24px 26px}
  .advantages .section-title{font-size:21px;line-height:1.25}
  .adv-list{list-style:none;margin-top:18px}
  .adv-list li{display:flex;align-items:center;gap:14px;font-size:15px;color:var(--ink);height:33px}
  .adv-list svg{flex:none}

  /* footer */
  .footer{position:absolute;left:0;top:1060px;width:440px;height:140px;background:var(--black);color:var(--white);display:flex;gap:18px;padding:24px 20px 0 24px;font-size:10.5px;line-height:1.55}
  .footer-dot{width:46px;height:46px;border-radius:50%;background:var(--green);flex:none}
  .footer-col{width:150px}
</style>
</head>
<body>
<main class="flyer">

  <section class="hero-panel">
    <div class="brand">
      <span class="brand-dot"></span>
      <div>
        <div class="brand-name">VOLTHAVEN</div>
        <div class="brand-tag">ELEKTRISCH VAREN</div>
      </div>
    </div>
    <h1 class="hero-title">BOATING<br><span class="accent">COMPANY</span></h1>
    <p class="hero-sub">From diesel to <b>high quality</b><br><b>electrical motor</b></p>
    <p class="hero-note">We only use <b>the best materials</b></p>
  </section>

  <div class="hero-photo" role="img" aria-label="Electric motorboat speeding through white water spray"></div>

  <section class="intro">
    <h2 class="section-title">Volthaven verbouwt boten</h2>
    <p class="body-copy">Neque porro quisquam est, qui dolorem ipsum <b>quia dolor sit amet, consectetur</b>, adipisci velit sed quia non numquam eius.</p>
  </section>

  <section class="pricing">
    <div class="plan">
      <div class="plan-card">
        <svg class="plan-icon" width="46" height="22" viewBox="0 0 46 22"><path d="M2 12h42l-7 8H9z M16 12V4h12l4 8" fill="none" stroke="#fff" stroke-width="2" stroke-linejoin="round"/></svg>
        <div class="plan-name">KLEIN</div>
        <div class="plan-size">4 tot 6 meter</div>
        <div class="plan-price"><div class="plan-from">vanaf</div><div class="plan-amount"><small>€</small>2200</div></div>
      </div>
      <p class="plan-note">Compleet ombouwpakket met motor en accu, inclusief montage</p>
    </div>
    <div class="plan">
      <div class="plan-card">
        <svg class="plan-icon" width="46" height="22" viewBox="0 0 46 22"><path d="M2 12h42l-7 8H9z M16 12V4h12l4 8" fill="none" stroke="#fff" stroke-width="2" stroke-linejoin="round"/></svg>
        <div class="plan-name">MIDDEL</div>
        <div class="plan-size">6 tot 8 meter</div>
        <div class="plan-price"><div class="plan-from">vanaf</div><div class="plan-amount"><small>€</small>12500</div></div>
      </div>
      <p class="plan-note">Inboard motor met accupakket en laadsysteem aan boord</p>
    </div>
    <div class="plan">
      <div class="plan-card">
        <svg class="plan-icon" width="46" height="22" viewBox="0 0 46 22"><path d="M2 12h42l-7 8H9z M16 12V4h12l4 8" fill="none" stroke="#fff" stroke-width="2" stroke-linejoin="round"/></svg>
        <div class="plan-name">GROOT</div>
        <div class="plan-size">8 tot 10 meter</div>
        <div class="plan-price"><div class="plan-from">vanaf</div><div class="plan-amount"><small>€</small>17500</div></div>
      </div>
      <p class="plan-note">Krachtige aandrijving tot 80 pk met ruime accucapaciteit</p>
    </div>
    <div class="plan">
      <div class="plan-card">
        <svg class="plan-icon" width="46" height="22" viewBox="0 0 46 22"><path d="M2 12h42l-7 8H9z M16 12V4h12l4 8" fill="none" stroke="#fff" stroke-width="2" stroke-linejoin="round"/></svg>
        <div class="plan-name">GROOT</div>
        <div class="plan-size">10 meter en meer</div>
        <div class="plan-price"><div class="plan-from">prijs</div><div class="plan-amount request">OP AANVRAAG</div></div>
      </div>
      <p class="plan-note">Maatwerk voor grotere schepen, vraag een offerte aan</p>
    </div>
  </section>

  <section class="solution">
    <h2 class="section-title">Best passende oplossing</h2>
    <p class="body-copy">Volthaven vervangt je oude motor voor een moderne elektromotor. <b>Om dat goed te kunnen</b> doen is het nodig dat wij je boot eerst leren kennen om zo tot de meest passende oplossing te komen.</p>
    <p class="body-copy">Neque porro quisquam est, qui dolorem ipsum <b>quia dolor sit amet, consectetur</b>, adipisci velit sed quia non numquam eius.</p>
  </section>

  <section class="advantages">
    <h2 class="section-title">Major advantages<br>of electric boating</h2>
    <ul class="adv-list">
      <li><svg width="24" height="24" viewBox="0 0 24 24"><circle cx="12" cy="12" r="12" fill="#8cc63f"/><path d="M7 12.5l3.2 3.2L17 9" fill="none" stroke="#fff" stroke-width="2"/></svg>Completely silent</li>
      <li><svg width="24" height="24" viewBox="0 0 24 24"><circle cx="12" cy="12" r="12" fill="#8cc63f"/><path d="M7 12.5l3.2 3.2L17 9" fill="none" stroke="#fff" stroke-width="2"/></svg>No fumes, smells or smoke</li>
      <li><svg width="24" height="24" viewBox="0 0 24 24"><circle cx="12" cy="12" r="12" fill="#8cc63f"/><path d="M7 12.5l3.2 3.2L17 9" fill="none" stroke="#fff" stroke-width="2"/></svg>Cheap to operate</li>
      <li><svg width="24" height="24" viewBox="0 0 24 24"><circle cx="12" cy="12" r="12" fill="#8cc63f"/><path d="M7 12.5l3.2 3.2L17 9" fill="none" stroke="#fff" stroke-width="2"/></svg>Environmentally friendly</li>
      <li><svg width="24" height="24" viewBox="0 0 24 24"><circle cx="12" cy="12" r="12" fill="#8cc63f"/><path d="M7 12.5l3.2 3.2L17 9" fill="none" stroke="#fff" stroke-width="2"/></svg>No maintenance</li>
      <li><svg width="24" height="24" viewBox="0 0 24 24"><circle cx="12" cy="12" r="12" fill="#8cc63f"/><path d="M7 12.5l3.2 3.2L17 9" fill="none" stroke="#fff" stroke-width="2"/></svg>More enjoyable</li>
    </ul>
  </section>

  <footer class="footer">
    <span class="footer-dot"></span>
    <div class="footer-col">Havenkade 12 1021AB<br>Amsterdam-Noord<br>Nederland</div>
    <div class="footer-col">+31 (0)6 12 34 56 78<br>info@volthaven.nl<br>www.volthaven.nl<br>KvK 12345678</div>
  </footer>

</main>
</body>
</html>
```